Maple Roster Business Card for recruitment company

We are looking for a Business Card Design that incorporates our personal details and our busines name and logo. We are a specialized search consultancy that recruit Property and Construction professionals.
We would like a business card that stands out and is appealing to the Construction and Property industry as well.

Target Market(s)

people in the construction and property industry

Contact Information for Business Card

Business Name and logo

Font styles to use
Serif

Colors
0094D4
00A9DD
6FCCEA
C7EBF8
E9F6FB

Requirements
Must have
• Business name and logo as well as contact details
Should not have
• No photos of us please

```html
<!DOCTYPE html>
<html lang="en">
<head>
<meta charset="utf-8">
<title>Maple Roster – Business Card</title>
<link rel="stylesheet" href="https://fonts.googleapis.com/css2?family=Didact+Gothic&family=Mulish:wght@700&display=swap">
<style>
  :root {
    --backdrop: #2b2c2d;
    --card-white: #f8f8f8;
    --card-white-shade: #efefef;
    --navy: #083448;
    --navy-deep: #062c3d;
    --ink-light: #ffffff;
    --rule: #5a7684;
  }
  * { box-sizing: border-box; margin: 0; padding: 0; }
  html, body { width: 1200px; height: 732px; overflow: hidden; }
  body {
    background: var(--backdrop);
    font-family: "Didact Gothic", sans-serif;
    position: relative;
  }
  .card {
    position: absolute;
    top: 242px;
    width: 436px;
    height: 248px;
    box-shadow: 0 6px 14px rgba(0,0,0,0.55);
    overflow: hidden;
  }
  .card--front {
    left: 144px;
    background: linear-gradient(160deg, var(--card-white) 40%, var(--card-white-shade) 100%);
  }
  .card--back {
    left: 621px;
    background: linear-gradient(160deg, var(--navy) 30%, var(--navy-deep) 100%);
    display: flex;
    align-items: center;
    justify-content: center;
  }
  .wordmark {
    position: absolute;
    left: 14px;
    top: 22px;
    font-size: 34px;
    line-height: 1;
    letter-spacing: 0.5px;
    color: var(--navy);
    text-transform: uppercase;
  }
  .rule {
    position: absolute;
    left: 14px;
    right: 15px;
    top: 164px;
    height: 1px;
    background: var(--rule);
  }
  .contact-band {
    position: absolute;
    left: 0; right: 0; bottom: 0;
    height: 71px;
    background: var(--navy);
    color: var(--ink-light);
    padding: 12px 15px 0 14px;
    display: flex;
    justify-content: space-between;
  }
  .person__name {
    font-family: "Mulish", sans-serif;
    font-weight: 700;
    font-size: 16px;
    line-height: 17px;
  }
  .person__role, .person__city,
  .contact-list li {
    font-size: 12.5px;
    line-height: 14.5px;
  }
  .contact-list {
    list-style: none;
    text-align: right;
    padding-top: 3px;
  }
  .contact-list b {
    font-family: "Mulish", sans-serif;
    font-weight: 700;
    display: inline-block;
    width: 16px;
    text-align: right;
  }
  .back-name {
    display: flex;
    align-items: center;
    gap: 12px;
    color: var(--ink-light);
    font-size: 28px;
    letter-spacing: 1px;
    text-transform: uppercase;
  }
  .back-name__dot {
    width: 14px; height: 14px;
    border-radius: 50%;
    background: var(--ink-light);
  }
</style>
</head>
<body>
  <section class="card card--front">
    <div class="wordmark">Maple Roster</div>
    <div class="rule"></div>
    <div class="contact-band">
      <div class="person">
        <p class="person__name">Harriet Quill</p>
        <p class="person__role">Director | Senior Search Consultant</p>
        <p class="person__city">Auckland, New Zealand</p>
      </div>
      <ul class="contact-list">
        <li>+64 27 408 2291 <b>:T</b></li>
        <li>harriet@mapleroster.nz <b>:E</b></li>
        <li>www.mapleroster.nz <b>:W</b></li>
      </ul>
    </div>
  </section>

  <section class="card card--back">
    <div class="back-name">
      <span class="back-name__dot"></span>
      <span>Maple Roster</span>
    </div>
  </section>
</body>
</html>
```